Business Card Design Project

We are an incubator company that helps young entrepreneur to launch new ideas into the market. We will be targeting investors or likewise; Angels, young entrepreneurs and technopreneurs.

Our logo is being tasked by pixelhive to design, therefore there is no logo for now.
You can us Lanternfield Pte Ltd as the logo for the time being.

Please let us have some versions of modern and yet professional designs; for words, you can indicate e.g (address), (Title)

thanks

Target Market(s)

young entrepreneurs
angels, investors

Industry/Entity Type

Business

Colors
3176b5
ffffff

Requirements
Must have
• able to project out our name; Lanternfield
Should not have
• Nothing childish or cartoon

```html
<!DOCTYPE html>
<html lang="en">
<head>
<meta charset="utf-8">
<title>Lanternfield Business Card</title>
<link href="https://fonts.googleapis.com/css2?family=Open+Sans:wght@400;600&display=swap" rel="stylesheet">
<style>
  :root {
    --backdrop: #8a8a85;
    --paper: #ffffff;
    --slate: #4a5166;
    --slate-deep: #434a5e;
    --teal: #0896bc;
    --contact-ink: #aab2c6;
    --ink: #3f4659;
  }
  * { margin: 0; padding: 0; box-sizing: border-box; }
  html, body {
    width: 1200px;
    height: 900px;
    overflow: hidden;
    background: var(--backdrop);
    font-family: "Open Sans", sans-serif;
  }
  .business-card {
    position: absolute;
    left: 100px;
    top: 170px;
    width: 1000px;
    height: 560px;
    background: var(--paper);
    overflow: hidden;
  }
  .card-shapes {
    position: absolute;
    inset: 0;
    width: 100%;
    height: 100%;
  }
  .brand-lockup {
    position: absolute;
    left: 48px;
    top: 52px;
    display: flex;
    align-items: center;
    gap: 14px;
  }
  .brand-dot {
    width: 34px;
    height: 34px;
    border-radius: 50%;
    background: var(--teal);
  }
  .brand-name {
    font-size: 34px;
    font-weight: 600;
    color: var(--ink);
    letter-spacing: 0.5px;
  }
  .brand-vertical {
    position: absolute;
    left: 1000px;
    top: 10px;
    transform-origin: 0 0;
    transform: rotate(90deg);
    font-size: 64px;
    font-weight: 600;
    line-height: 1;
    color: var(--ink);
    white-space: nowrap;
    letter-spacing: 1px;
  }
  .holder {
    position: absolute;
    left: 500px;
    top: 200px;
    color: var(--paper);
  }
  .holder-name {
    font-size: 38px;
    font-weight: 400;
    line-height: 1;
  }
  .holder-title {
    font-size: 15px;
    color: var(--teal);
    margin-left: 92px;
    margin-top: 2px;
  }
  .contact-box {
    position: absolute;
    left: 430px;
    top: 305px;
    width: 360px;
    height: 112px;
    background: var(--slate-deep);
    display: flex;
    flex-direction: column;
    align-items: center;
    justify-content: center;
    color: var(--contact-ink);
    font-size: 22px;
    line-height: 1.35;
  }
</style>
</head>
<body>
  <div class="business-card">
    <svg class="card-shapes" viewBox="0 0 1000 560" aria-hidden="true">
      <path fill="var(--teal)" d="M290,345 C320,160 450,60 600,60 C690,60 760,88 810,128 C850,88 920,68 1000,76 L1000,560 L950,560 Z"/>
      <path fill="var(--slate)" d="M0,445 C110,375 230,345 300,348 C322,185 450,82 600,82 C760,82 880,175 925,310 L955,560 L0,560 Z"/>
    </svg>

    <div class="brand-lockup">
      <span class="brand-dot"></span>
      <span class="brand-name">Lanternfield</span>
    </div>

    <div class="brand-vertical">lanternfield</div>

    <div class="holder">
      <p class="holder-name">Your name</p>
      <p class="holder-title">designation</p>
    </div>

    <div class="contact-box">
      <span>contact@lanternfield.com</span>
      <span>lanternfield.com</span>
    </div>
  </div>
</body>
</html>
```